Verodex business card

Business card for sustainable investment company called "Verodex". Verodex is an exchange platform selling carbon credits between buyers and sellers. Carbon Credits are an environmental commodity for reducing global carbon emissions.

the card should obviously have our logo and the theme should be sustainability/environment mixed with a trading platform.

Contact Information for Business Card

Logo, Name, Title, Phone, Email

Colors
0054AA
0677BA
7BADD7
CADEEF
E8F1F8
0094D4
00A9DD
6FCCEA
C7EBF8
E9F6FB
00AB8E
00BBA5
67D7C9
C6EFE9
E9F9F6
59FF00
82FF00
B8FF75
E3FFCB
F4FFEA

```html
<!DOCTYPE html>
<html lang="en">
<head>
<meta charset="utf-8">
<title>Verodex business card</title>
<link href="https://fonts.googleapis.com/css2?family=Montserrat:wght@400;500;700&display=swap" rel="stylesheet">
<style>
  :root {
    --backdrop: #e9e9eb;
    --navy: #1d2b4c;
    --sky: #36b5e5;
    --icon-blue: #2f8fd8;
    --grad-start: #6ecadb;
    --grad-mid: #32bde9;
    --grad-end: #4066b4;
    --paper: #ffffff;
  }
  * { box-sizing: border-box; margin: 0; padding: 0; }
  html, body {
    width: 1200px; height: 900px; overflow: hidden;
    background: var(--backdrop);
    font-family: "Montserrat", sans-serif;
  }
  .canvas { position: relative; width: 1200px; height: 900px; }
  .card {
    position: absolute;
    width: 560px; height: 320px;
    border-radius: 2px;
    box-shadow: 0 14px 30px rgba(0,0,0,0.14), 0 2px 4px rgba(0,0,0,0.08);
  }
  .card-front {
    left: 70px; top: 100px;
    background: linear-gradient(30deg, var(--grad-start) 0%, var(--grad-mid) 45%, var(--grad-end) 100%);
    display: flex; align-items: center; justify-content: center;
  }
  .brand { display: flex; align-items: center; gap: 16px; }
  .brand-square { width: 34px; height: 34px; }
  .brand-name { font-weight: 700; letter-spacing: 2px; text-transform: uppercase; }
  .card-front .brand-square { background: var(--paper); }
  .card-front .brand-name { color: var(--paper); font-size: 50px; }

  .card-back {
    left: 570px; top: 480px;
    background: var(--paper);
    padding: 34px 38px;
  }
  .card-back .brand { position: absolute; left: 38px; top: 40px; gap: 12px; }
  .card-back .brand-square { width: 26px; height: 26px; background: var(--icon-blue); }
  .card-back .brand-name { color: var(--navy); font-size: 30px; }

  .person { position: absolute; right: 38px; top: 118px; text-align: right; }
  .person-name { font-size: 21px; font-weight: 700; letter-spacing: 0.5px; color: var(--navy); }
  .person-name .surname { color: var(--sky); }
  .person-title { font-size: 14px; font-weight: 500; color: var(--navy); margin-top: 2px; }

  .contacts { position: absolute; left: 38px; bottom: 30px; list-style: none; }
  .contacts li {
    display: flex; align-items: center; gap: 10px;
    font-size: 15px; font-weight: 500; color: var(--navy);
    line-height: 26px;
  }
  .contacts svg { width: 15px; height: 15px; fill: var(--icon-blue); flex: none; }
</style>
</head>
<body>
<main class="canvas">
  <section class="card card-front" aria-label="Card front">
    <div class="brand">
      <span class="brand-square"></span>
      <span class="brand-name">Verodex</span>
    </div>
  </section>

  <section class="card card-back" aria-label="Card back">
    <div class="brand">
      <span class="brand-square"></span>
      <span class="brand-name">Verodex</span>
    </div>

    <div class="person">
      <p class="person-name">ADRIAN <span class="surname">KESSLER</span></p>
      <p class="person-title">Co-Founder</p>
    </div>

    <ul class="contacts">
      <li>
        <svg viewBox="0 0 24 24" aria-hidden="true"><path d="M6.6 10.8a15.1 15.1 0 0 0 6.6 6.6l2.2-2.2c.3-.3.7-.4 1-.2 1.1.4 2.3.6 3.6.6.6 0 1 .4 1 1V20c0 .6-.4 1-1 1A17 17 0 0 1 3 4c0-.6.4-1 1-1h3.5c.6 0 1 .4 1 1 0 1.3.2 2.5.6 3.6.1.3 0 .7-.2 1z"/></svg>
        555-210-4836
      </li>
      <li>
        <svg viewBox="0 0 24 24" aria-hidden="true"><path d="M2 5h20v14H2z M3.5 6.5 12 13l8.5-6.5" stroke="#fff" stroke-width="1.5"/></svg>
        info@verodex.com
      </li>
      <li>
        <svg viewBox="0 0 24 24" aria-hidden="true"><circle cx="12" cy="12" r="10"/><path d="M2 12h20M12 2c3 3 3 17 0 20M12 2c-3 3-3 17 0 20" stroke="#fff" stroke-width="1.3" fill="none"/></svg>
        www.verodex.com
      </li>
    </ul>
  </section>
</main>
</body>
</html>
```